Heritage Hollow Business Cards

Require a business card design. <br/><br/>Needs to include logo (either round or long version) plus these details:<br/>Maya Torvell<br/>Heritage Hollow<br/>maya@kelvadtrading.com.au<br/>02 6481 7395<br/>PO Box Glenwarra NSW 2791<br/>www.heritagehollow.com.au<br/><br/>I need in an editable format so that I can create for multiple staff members. <br/><br/>

Target Market(s)

We are an online store selling renovation products to home owners are builders. Looking for a classic classy design.

Industry/Entity Type

Home And Garden

Contact Information for Business Card

Maya Torvell
Heritage Hollow
maya@kelvadtrading.com.au
02 6481 7395
PO Box Glenwarra NSW 2791
www.heritagehollow.com.au

Colors

Designer to choose colors to be used in the design.

Requirements
Must have
• Must include Logo.

```html
<!DOCTYPE html>
<html lang="en">
<head>
<meta charset="utf-8">
<title>Heritage Hollow Business Cards</title>
<link rel="stylesheet" href="https://fonts.googleapis.com/css2?family=Quicksand:wght@500;600;700&display=swap">
<style>
  :root {
    --backdrop: #3b3937;
    --heritage-green: #54735f;
    --deep-green: #3f5a48;
    --paper: #ffffff;
    --ink: #1f1f1f;
  }
  * { margin: 0; padding: 0; box-sizing: border-box; }
  html, body { width: 1200px; height: 900px; overflow: hidden; }
  body {
    background: var(--backdrop);
    font-family: "Quicksand", sans-serif;
    position: relative;
  }
  .card {
    position: absolute;
    left: 311px;
    width: 576px;
    height: 329px;
    overflow: hidden;
    box-shadow: 0 6px 14px rgba(0,0,0,0.35);
  }
  .card-front { top: 98px; background: var(--heritage-green); }
  .card-back { top: 472px; background: var(--paper); }

  .front-ring {
    position: absolute;
    left: 22px; top: 12px;
    width: 356px; height: 356px;
    border: 2px solid var(--deep-green);
    border-radius: 50%;
  }
  .front-name {
    position: absolute;
    left: 75px; top: 198px;
    font-size: 44px;
    font-weight: 600;
    color: var(--paper);
    letter-spacing: 0.5px;
  }
  .front-url {
    position: absolute;
    left: 76px; top: 253px;
    font-size: 14px;
    font-weight: 600;
    color: var(--paper);
  }

  .back-mark {
    position: absolute;
    left: 195px; top: 10px;
    width: 172px; height: 172px;
    border: 1.5px solid var(--ink);
    border-radius: 50%;
    display: flex;
    align-items: center;
    justify-content: center;
    text-align: center;
  }
  .back-mark-name {
    font-size: 22px;
    font-weight: 700;
    line-height: 1.05;
    color: var(--ink);
  }
  .holder {
    position: absolute;
    right: 312px; top: 212px;
    text-align: right;
    font-size: 14px;
    line-height: 19px;
    color: var(--ink);
  }
  .holder-name { font-weight: 700; font-size: 15px; color: var(--heritage-green); }
  .holder-address { color: var(--heritage-green); font-weight: 500; margin-top: 4px; }
  .divider {
    position: absolute;
    left: 284px; top: 213px;
    width: 1.5px; height: 77px;
    background: var(--ink);
  }
  .contact-list {
    position: absolute;
    left: 299px; top: 216px;
    list-style: none;
    font-size: 15px;
    font-weight: 500;
    color: var(--ink);
  }
  .contact-list li {
    display: flex;
    align-items: center;
    gap: 8px;
    height: 26px;
  }
  .contact-list svg { width: 17px; height: 17px; fill: var(--heritage-green); flex: none; }
  .back-band {
    position: absolute;
    left: 0; bottom: 0;
    width: 100%; height: 12px;
    background: var(--heritage-green);
  }
</style>
</head>
<body>
  <section class="card card-front">
    <div class="front-ring"></div>
    <div class="front-name">Heritage Hollow</div>
    <div class="front-url">www.heritagehollow.com.au</div>
  </section>

  <section class="card card-back">
    <div class="back-mark"><span class="back-mark-name">Heritage<br>Hollow</span></div>

    <div class="holder">
      <div class="holder-name">Maya Torvell</div>
      <div>Heritage Hollow</div>
      <div class="holder-address">PO Box<br>Glenwarra NSW 2791</div>
    </div>

    <div class="divider"></div>

    <ul class="contact-list">
      <li>
        <svg viewBox="0 0 24 24" aria-hidden="true"><path d="M6.6 10.8a15.1 15.1 0 0 0 6.6 6.6l2.2-2.2c.3-.3.7-.4 1-.2 1.1.4 2.3.6 3.6.6.6 0 1 .4 1 1V20c0 .6-.4 1-1 1A17 17 0 0 1 3 4c0-.6.4-1 1-1h3.5c.6 0 1 .4 1 1 0 1.3.2 2.5.6 3.6.1.3 0 .7-.2 1l-2.3 2.2z"/></svg>
        <span>02 6481 7395</span>
      </li>
      <li>
        <svg viewBox="0 0 24 24" aria-hidden="true"><path d="M2 5h20v2l-10 6L2 7z"/><path d="M2 9l10 6 10-6v10H2z"/></svg>
        <span>maya@kelvadtrading.com.au</span>
      </li>
      <li>
        <svg viewBox="0 0 24 24" aria-hidden="true"><circle cx="12" cy="12" r="10"/><path d="M12 2v20M2 12h20" stroke="#fff" stroke-width="1.5" fill="none"/></svg>
        <span>www.heritagehollow.com.au</span>
      </li>
    </ul>

    <div class="back-band"></div>
  </section>
</body>
</html>
```